New Innovative Counselling and psychotherapy Service needs Business Card design

Keep it simple and professional. On one side, just company name and logo (perhaps in all blue) and maybe a tag line.

On other side (all white) my name and Qualifications in centre

Industry/Entity Type

Health And Wellness

Contact Information for Business Card

Dara Whelby
Counsellor & Psychotherapist
BSc (Psychol.), BA, Dip. (Couns. & Psych.), PG.Cert (CBT), FGTrK, ONRE

I will also require Mobile no, Email and web site address of which I'll pass on to final designer.

Font styles to use
Sans Serif

Requirements
Must have
• My Logo Only and please use the colours in logo that is in it.
Should not have
• Any other images

```html
<!DOCTYPE html>
<html lang="en">
<head>
<meta charset="utf-8">
<title>Kestrel Avenue – Business Card</title>
<link href="https://fonts.googleapis.com/css2?family=Roboto:wght@300;400;700&display=swap" rel="stylesheet">
<style>
  :root {
    --sky: #52b8ec;
    --sky-deep: #47a8dc;
    --leaf: #8cc35a;
    --ink: #333638;
    --paper: #ffffff;
    --backdrop: #e6e7e8;
  }
  * { margin: 0; padding: 0; box-sizing: border-box; }
  html, body { width: 1200px; height: 726px; overflow: hidden; }
  body {
    background: var(--backdrop);
    font-family: "Roboto", Arial, sans-serif;
    position: relative;
  }
  .card {
    position: absolute;
    top: 208px;
    width: 530px;
    height: 310px;
    overflow: hidden;
    box-shadow: 0 4px 14px rgba(0,0,0,0.12);
  }
  .card--front { left: 50px; background: var(--sky); }
  .card--back { left: 620px; background: var(--paper); }

  .front-brand {
    position: absolute;
    left: 0; right: 0; top: 112px;
    display: flex;
    align-items: center;
    justify-content: center;
    gap: 18px;
  }
  .brand-dot {
    width: 58px; height: 58px;
    border-radius: 50%;
    background: var(--paper);
  }
  .front-name {
    color: var(--paper);
    font-size: 34px;
    font-weight: 400;
    letter-spacing: 0.5px;
    line-height: 1;
  }
  .front-tagline {
    color: var(--paper);
    font-size: 13px;
    font-weight: 400;
    letter-spacing: 6px;
    margin-top: 6px;
  }

  .back-decor {
    position: absolute;
    left: -110px; bottom: -150px;
    width: 370px; height: 370px;
    border-radius: 50%;
    background: var(--sky-deep);
  }
  .back-name {
    position: absolute;
    right: 28px; top: 26px;
    color: var(--ink);
    font-size: 30px;
    font-weight: 400;
  }
  .holder {
    position: absolute;
    right: 28px; top: 84px;
    text-align: right;
    color: var(--ink);
  }
  .holder-name {
    color: var(--sky);
    font-size: 20px;
    font-weight: 700;
    margin-bottom: 4px;
  }
  .holder-role, .holder-quals {
    font-size: 11px;
    line-height: 1.4;
  }
  .contact {
    position: absolute;
    right: 28px; top: 190px;
    list-style: none;
    text-align: right;
    color: var(--ink);
    font-size: 12px;
    line-height: 1.75;
  }
  .contact li { display: flex; justify-content: flex-end; align-items: center; gap: 7px; }
  .contact svg { width: 11px; height: 11px; }
</style>
</head>
<body>
  <section class="card card--front">
    <div class="front-brand">
      <span class="brand-dot"></span>
      <div>
        <div class="front-name">Kestrel Avenue</div>
        <div class="front-tagline">A tag line goes here</div>
      </div>
    </div>
  </section>

  <section class="card card--back">
    <div class="back-decor"></div>
    <div class="back-name">Kestrel Avenue</div>
    <div class="holder">
      <div class="holder-name">Dara Whelby</div>
      <div class="holder-role">Counsellor &amp; Psychotherapist</div>
      <div class="holder-quals">BSc (Psychol.), BA, Dip. (Couns. &amp;<br>Psych.), PG.Cert (CBT), FGTrK, ONRE</div>
    </div>
    <ul class="contact">
      <li>0161 482 3907
        <svg viewBox="0 0 12 12" aria-hidden="true"><path d="M2 1h3l1 3-2 1a7 7 0 0 0 3 3l1-2 3 1v3c-6 0-10-4-10-10z" fill="#3aa6a0"/></svg>
      </li>
      <li>dara.w@KestrelAvenue.com
        <svg viewBox="0 0 12 12" aria-hidden="true"><rect x="0.5" y="2" width="11" height="8" fill="#8cc35a"/><path d="M0.5 2l5.5 4.5L11.5 2" stroke="#fff" fill="none"/></svg>
      </li>
      <li>www.KestrelAvenue.com
        <svg viewBox="0 0 12 12" aria-hidden="true"><circle cx="6" cy="6" r="5.3" fill="#8cc35a"/><path d="M0.7 6h10.6M6 0.7c-3 3-3 7.6 0 10.6M6 0.7c3 3 3 7.6 0 10.6" stroke="#fff" stroke-width="0.8" fill="none"/></svg>
      </li>
    </ul>
  </section>
</body>
</html>
```